professional business card design for technology company

We are a small technology consulting firm, specialising in consulting based around Cloud and Managed services. Our colour scheme is yellow, blue and white, as you can see in the logos. Although we are based in melbourne australia, due to the nature of our work, our clients can be located anywhere. We are looking for a clean, professional, positive look - similar to our company logo

Target Market(s)

small business

Industry/Entity Type

Business

Contact Information for Business Card

eye catching, designed to incorporate some level of raised printing. Must contain website address, phone number, name and job title

Requirements
Must have
• Logo (attached) - use of the same colour scheme

```html
<!DOCTYPE html>
<html lang="en">
<head>
<meta charset="utf-8">
<title>Nubelia Business Card</title>
<link rel="stylesheet" href="https://fonts.googleapis.com/css2?family=Lato:wght@400;700&family=Arimo:wght@400&display=swap">
<style>
  :root {
    --backdrop: #d8e0df;
    --sky: #51d1fd;
    --paper: #ffffff;
    --ink: #3e4648;
    --white: #ffffff;
  }
  * { margin: 0; padding: 0; box-sizing: border-box; }
  html, body {
    width: 1200px; height: 864px; overflow: hidden;
    background: var(--backdrop);
  }
  .canvas { position: relative; width: 1200px; height: 864px; }

  .card { position: absolute; width: 527px; height: 310px; overflow: hidden; }
  .card--front { left: 332px; top: 93px; background: var(--paper); }
  .card--back { left: 334px; top: 450px; background: var(--sky); }

  .contact-panel {
    position: absolute; left: 0; top: 0; width: 262px; height: 100%;
    background: var(--sky); color: var(--white);
  }
  .person-name {
    position: absolute; left: 27px; top: 47px;
    font: 700 26px/1 "Lato", sans-serif; letter-spacing: 0.2px;
  }
  .person-title {
    position: absolute; left: 27px; top: 79px;
    font: 400 16px/1 "Lato", sans-serif; opacity: 0.95;
  }
  .contact-list {
    position: absolute; left: 27px; top: 143px; list-style: none;
    font: 400 14px/1.2 "Arimo", sans-serif;
  }
  .contact-list li { display: flex; align-items: flex-start; height: 22.5px; }
  .contact-list .icon { width: 10px; height: 10px; margin: 3px 6px 0 0; flex: none; }
  .contact-list .address { height: auto; }
  .contact-list .address span { display: block; }

  .brand {
    position: absolute; display: flex; align-items: center;
    font-family: "Lato", sans-serif; font-weight: 700;
  }
  .brand--front { left: 281px; top: 138px; color: var(--ink); font-size: 36px; }
  .brand--front .brand-dot { width: 40px; height: 40px; background: var(--sky); margin-right: 14px; }
  .brand--back { left: 124px; top: 133px; color: var(--white); font-size: 48px; }
  .brand--back .brand-dot { width: 52px; height: 52px; background: var(--white); margin-right: 18px; }
  .brand-dot { border-radius: 50%; flex: none; }
</style>
</head>
<body>
<main class="canvas">
  <section class="card card--front">
    <div class="contact-panel">
      <h1 class="person-name">John Smith</h1>
      <p class="person-title">Managing Director</p>
      <ul class="contact-list">
        <li><svg class="icon" viewBox="0 0 10 10"><path d="M1 3.5 Q5 0.5 9 3.5 L8 5 L6.5 4 L6.5 3 Q5 2.5 3.5 3 L3.5 4 L2 5 Z M2 5.5 H8 V8.5 H2 Z" fill="currentColor"/></svg>044-123 456 789</li>
        <li><svg class="icon" viewBox="0 0 10 10"><rect x="2.5" y="0.5" width="5" height="9" rx="1" fill="none" stroke="currentColor" stroke-width="1.2"/></svg>044-123 456 789</li>
        <li><svg class="icon" viewBox="0 0 10 10"><rect x="0.5" y="2" width="9" height="6" fill="currentColor"/><path d="M0.5 2 L5 5.5 L9.5 2" fill="none" stroke="#51d1fd" stroke-width="0.8"/></svg>info@webname.com</li>
        <li><svg class="icon" viewBox="0 0 10 10"><path d="M4 6 L6 4 M3 5 L1.5 6.5 a1.4 1.4 0 0 0 2 2 L5 7 M7 5 L8.5 3.5 a1.4 1.4 0 0 0 -2 -2 L5 3" fill="none" stroke="currentColor" stroke-width="1.1"/></svg>www.websitename.com</li>
        <li class="address"><svg class="icon" viewBox="0 0 10 10"><path d="M5 0.5 a3 3 0 0 1 3 3 C8 6 5 9.5 5 9.5 C5 9.5 2 6 2 3.5 a3 3 0 0 1 3 -3 Z M5 2.5 a1 1 0 1 0 0.01 0 Z" fill="currentColor" fill-rule="evenodd"/></svg><div><span>12345, Address Goes Here</span><span>&nbsp;&nbsp;Country Name, 123456</span></div></li>
      </ul>
    </div>
    <div class="brand brand--front"><span class="brand-dot"></span>Nubelia</div>
  </section>

  <section class="card card--back">
    <div class="brand brand--back"><span class="brand-dot"></span>Nubelia</div>
  </section>
</main>
</body>
</html>
```